Bref créative
Stationary Package for Corran Builders LLC
Business Card, Letterhead, envelope, fax, invoice, folder, yard marketing signage
Professional
Martin Olvey
PO Box 317946
Houston, TX 77391
corranbuilders@mailvessa.com
www.corranbuilders-demo.net

```html
<!DOCTYPE html>
<html lang="en">
<head>
<meta charset="utf-8">
<title>Corran Builders LLC – Business Card Options</title>
<link rel="stylesheet" href="https://fonts.googleapis.com/css2?family=Michroma&family=Open+Sans:wght@400;600&display=swap">
<style>
  :root {
    --board: #2a2a2a;
    --card: #ffffff;
    --ink: #4a4a4a;
    --ink-soft: #6d6d6d;
    --orange: #e4552b;
    --rule: #d4d4d4;
    --caption: #e6e6e6;
    --ghost: #f1e6e2;
  }
  * { margin: 0; padding: 0; box-sizing: border-box; }
  html, body { width: 1200px; height: 809px; overflow: hidden; background: var(--board); }
  .board { position: relative; width: 1200px; height: 809px; background: var(--board); font-family: "Open Sans", sans-serif; color: var(--ink); }
  .card { position: absolute; background: var(--card); border-radius: 22px; overflow: hidden; box-shadow: 0 3px 10px rgba(0,0,0,.45); }
  .card--front-a { left: 34px; top: 43px; width: 570px; height: 341px; }
  .card--front-b { left: 636px; top: 43px; width: 540px; height: 341px; }
  .card--back-a  { left: 34px; top: 461px; width: 570px; height: 312px; }
  .card--back-b  { left: 636px; top: 461px; width: 540px; height: 312px; }
  .caption { position: absolute; font-family: "Michroma", sans-serif; font-size: 17px; letter-spacing: 3px; color: var(--caption); text-align: center; white-space: nowrap; }
  .caption--front-a { left: 34px; width: 570px; top: 405px; }
  .caption--front-b { left: 636px; width: 540px; top: 405px; }
  .caption--back-a  { left: 34px; width: 570px; top: 781px; }
  .caption--back-b  { left: 636px; width: 540px; top: 781px; }

  .brand { position: absolute; display: flex; align-items: center; gap: 10px; font-family: "Michroma", sans-serif; color: var(--ink); white-space: nowrap; }
  .brand__square { width: 22px; height: 22px; background: var(--orange); flex: none; }
  .card--front-a .brand { left: 0; right: 0; top: 140px; justify-content: center; font-size: 26px; }
  .card--front-b .brand { left: 22px; top: 156px; font-size: 13px; gap: 7px; }
  .card--front-b .brand__square { width: 14px; height: 14px; }
  .card--back-a .brand { left: 0; right: 0; top: 108px; justify-content: center; font-size: 24px; }

  .accent-bar { position: absolute; background: var(--orange); }
  .card--front-a .accent-bar { left: 0; top: 232px; width: 10px; height: 78px; }
  .card--front-b .accent-bar { left: 290px; top: 58px; width: 4px; height: 40px; }
  .divider { position: absolute; left: 292px; top: 58px; width: 1px; height: 230px; background: var(--rule); }

  .person__name { color: var(--orange); font-size: 15px; font-weight: 600; }
  .person__role { font-size: 12px; color: var(--ink-soft); margin-bottom: 16px; }
  .person__address { font-size: 12px; color: var(--ink-soft); font-style: italic; line-height: 1.45; }
  .card--front-a .person { position: absolute; left: 180px; top: 238px; text-align: left; }
  .card--front-a .person__role { margin-bottom: 14px; }

  .contacts { list-style: none; font-size: 12px; color: var(--ink-soft); line-height: 1.55; white-space: nowrap; }
  .contacts li { display: flex; align-items: center; gap: 8px; }
  .contacts svg { width: 11px; height: 11px; flex: none; fill: var(--orange); }
  .card--front-a .contacts { position: absolute; left: 360px; top: 230px; }
  .card--front-b .stack { position: absolute; left: 306px; top: 58px; }
  .card--front-b .person__address { margin-bottom: 16px; }

  .url { position: absolute; left: 0; right: 0; text-align: center; font-size: 17px; letter-spacing: 3px; color: var(--ink); }
  .card--back-a .url { top: 200px; }
  .card--back-b .url { top: 142px; }
  .ghost-name { position: absolute; left: 0; right: 0; top: 80px; text-align: center; font-family: "Michroma", sans-serif; font-size: 42px; color: var(--ghost); white-space: nowrap; }
</style>
</head>
<body>
<main class="board">

  <section class="card card--front-a" aria-label="Business card front, option A">
    <div class="brand"><span class="brand__square"></span>Corran Builders LLC</div>
    <span class="accent-bar"></span>
    <div class="person">
      <p class="person__name">Martin Olvey</p>
      <p class="person__role">President</p>
      <p class="person__address">PO Box 317946 Houston,<br>TX 77391</p>
    </div>
    <ul class="contacts">
      <li><svg viewBox="0 0 12 12"><path d="M2 1h3l1 3-2 1a6 6 0 0 0 3 3l1-2 3 1v3c-6 0-9-3-9-9z"/></svg>832-555-0146</li>
      <li><svg viewBox="0 0 12 12"><rect x="3" y="0" width="6" height="12" rx="1"/></svg>832-555-0186</li>
      <li><svg viewBox="0 0 12 12"><rect x="1" y="4" width="10" height="7"/><rect x="3" y="1" width="6" height="3"/></svg>713-555-0140</li>
      <li><svg viewBox="0 0 12 12"><circle cx="6" cy="6" r="6"/></svg>corranbuilders@mailvessa.com</li>
      <li><svg viewBox="0 0 12 12"><circle cx="6" cy="6" r="6"/></svg>www.corranbuilders-demo.net</li>
    </ul>
  </section>
  <p class="caption caption--front-a">Business Card Front Option A</p>

  <section class="card card--front-b" aria-label="Business card front, option B">
    <div class="brand"><span class="brand__square"></span>Corran Builders LLC</div>
    <span class="divider"></span>
    <span class="accent-bar"></span>
    <div class="stack">
      <div class="person">
        <p class="person__name">Martin Olvey</p>
        <p class="person__role">President</p>
        <p class="person__address">PO Box 317946 Houston,<br>TX 77391</p>
      </div>
      <ul class="contacts">
        <li><svg viewBox="0 0 12 12"><path d="M2 1h3l1 3-2 1a6 6 0 0 0 3 3l1-2 3 1v3c-6 0-9-3-9-9z"/></svg>832-555-0146</li>
        <li><svg viewBox="0 0 12 12"><rect x="3" y="0" width="6" height="12" rx="1"/></svg>832-555-0186</li>
        <li><svg viewBox="0 0 12 12"><rect x="1" y="4" width="10" height="7"/><rect x="3" y="1" width="6" height="3"/></svg>713-555-0140</li>
        <li><svg viewBox="0 0 12 12"><circle cx="6" cy="6" r="6"/></svg>corranbuilders@mailvessa.com</li>
        <li><svg viewBox="0 0 12 12"><circle cx="6" cy="6" r="6"/></svg>www.corranbuilders-demo.net</li>
      </ul>
    </div>
  </section>
  <p class="caption caption--front-b">Business Card Front Option B</p>

  <section class="card card--back-a" aria-label="Business card back, option A">
    <div class="brand"><span class="brand__square"></span>Corran Builders LLC</div>
    <p class="url">www.corranbuilders-demo.net</p>
  </section>
  <p class="caption caption--back-a">Business Card Back Option A</p>

  <section class="card card--back-b" aria-label="Business card back, option B">
    <p class="ghost-name" aria-hidden="true">Corran Builders</p>
    <p class="url">www.corranbuilders-demo.net</p>
  </section>
  <p class="caption caption--back-b">Business Card Back Option B</p>

</main>
</body>
</html>
```